KTR Design Business Card

I need to develop a business card for my real estate design and investment company. Something clean, classic and professional with a modern vibe.

Industry/Entity Type

Real Estate

Font styles to use
Serif
Sans Serif

```html
<!DOCTYPE html>
<html lang="en">
<head>
<meta charset="utf-8">
<title>KTR Design Business Card</title>
<link rel="stylesheet" href="https://fonts.googleapis.com/css2?family=Orbitron:wght@600&family=Saira:wght@300;400&display=swap">
<style>
  :root {
    --page: #e9e7e4;
    --card-dark: #383838;
    --card-light: #ffffff;
    --rim: #a9a9a9;
    --ink-dark: #2e2e2e;
    --ink-light: #ffffff;
  }
  * { margin: 0; padding: 0; box-sizing: border-box; }
  html, body { width: 1200px; height: 901px; overflow: hidden; background: var(--page); }
  .canvas { position: relative; width: 1200px; height: 901px; }
  .card {
    position: absolute; left: 150px; top: 193px;
    width: 900px; height: 514px;
    border-radius: 44px; overflow: hidden;
    background: var(--card-dark);
    box-shadow: 0 10px 30px rgba(0,0,0,0.18);
  }
  .card-shapes { position: absolute; inset: 0; }
  .brand-block { position: absolute; left: 190px; top: 78px; }
  .brand {
    font-family: "Saira", sans-serif; font-weight: 300;
    font-size: 70px; line-height: 1; letter-spacing: 4px; color: var(--ink-dark);
  }
  .tagline {
    margin-top: 10px;
    font-family: "Saira", sans-serif; font-weight: 300;
    font-size: 22px; letter-spacing: 0.5px; color: var(--ink-dark);
  }
  .holder { position: absolute; left: 72px; top: 262px; font-family: "Orbitron", sans-serif; font-weight: 600; color: var(--ink-dark); }
  .holder-name { font-size: 26px; letter-spacing: 2px; }
  .holder-role { font-size: 18px; letter-spacing: 2px; margin-top: 4px; }
  .contacts {
    position: absolute; right: 44px; bottom: 48px;
    list-style: none; text-align: right;
    font-family: "Saira", sans-serif; font-weight: 400;
    font-size: 19px; letter-spacing: 1.5px; color: var(--ink-light);
  }
  .contacts li { display: flex; align-items: center; justify-content: flex-end; gap: 10px; height: 32px; }
  .icon { width: 22px; height: 22px; flex: none; }
</style>
</head>
<body>
<div class="canvas">
  <div class="card">
    <svg class="card-shapes" width="900" height="514" viewBox="0 0 900 514" aria-hidden="true">
      <defs>
        <linearGradient id="faceShade" x1="0" y1="0" x2="1" y2="1">
          <stop offset="0" stop-color="#ffffff"/>
          <stop offset="1" stop-color="#ececec"/>
        </linearGradient>
      </defs>
      <ellipse cx="330" cy="140" rx="540" ry="240" transform="rotate(-6 330 140)" fill="var(--rim)"/>
      <ellipse cx="325" cy="128" rx="528" ry="232" transform="rotate(-6 325 128)" fill="url(#faceShade)"/>
    </svg>
    <div class="brand-block">
      <div class="brand">KTR Design</div>
      <div class="tagline">Design and Productions</div>
    </div>
    <div class="holder">
      <div class="holder-name">DANIEL BROOKS</div>
      <div class="holder-role">FINANCIAL ADVISOR</div>
    </div>
    <ul class="contacts">
      <li>012 555 0147
        <svg class="icon" viewBox="0 0 22 22"><circle cx="11" cy="11" r="11" fill="#fff"/><path d="M7 6.5c1-.8 1.8-.6 2.3.4l.6 1.3c.2.6 0 1-.5 1.4.5 1.3 1.4 2.2 2.7 2.8.4-.5.9-.7 1.4-.5l1.3.6c1 .5 1.2 1.3.4 2.2-2.8 2.4-10.2-4.6-8.2-8.2z" fill="#383838"/></svg></li>
      <li>012 555 0147
        <svg class="icon" viewBox="0 0 22 22"><circle cx="11" cy="11" r="11" fill="#fff"/><rect x="7.5" y="5" width="7" height="12" rx="1.3" fill="#383838"/><rect x="8.7" y="6.5" width="4.6" height="7.5" fill="#fff"/></svg></li>
      <li>hello@ktrstudio.com
        <svg class="icon" viewBox="0 0 22 22"><circle cx="11" cy="11" r="11" fill="#fff"/><rect x="5.5" y="7" width="11" height="8" rx="1" fill="#383838"/><path d="M5.8 7.5 11 11.5l5.2-4" stroke="#fff" stroke-width="1" fill="none"/></svg></li>
      <li>www.ktrstudio.com
        <svg class="icon" viewBox="0 0 22 22"><circle cx="11" cy="11" r="11" fill="#fff"/><circle cx="11" cy="11" r="5.5" fill="none" stroke="#383838" stroke-width="1.3"/><ellipse cx="11" cy="11" rx="2.3" ry="5.5" fill="none" stroke="#383838" stroke-width="1.1"/><path d="M5.5 11h11" stroke="#383838" stroke-width="1.1"/></svg></li>
      <li>Suite 4.27 Harbor View Road NRD
        <svg class="icon" viewBox="0 0 22 22"><circle cx="11" cy="11" r="11" fill="#fff"/><path d="M11 17.5s-4-4.4-4-7.3a4 4 0 0 1 8 0c0 2.9-4 7.3-4 7.3z" fill="#383838"/><circle cx="11" cy="10.2" r="1.5" fill="#fff"/></svg></li>
    </ul>
  </div>
</div>
</body>
</html>
```